Hardcore nerd needs to stand out in a sea of dull Defence business cards

Wombarra Devices is a new Australian consulting engineering company that turns research and theory into practical systems. No evangelistic fluff, just mathematics and physics into electronic and optical circuits for consumer products, scientific research or Defence applications.

We already have a recognised logo (provided) which is often dark blue/black on a light background but we're open to other combinations. (Us engineers tend to have limited aesthetic imagination :)

Some of our recent products have included:
* Instrumentation for electrical testing,
* Radar jammers,
* GPS antenna design,
* Satellite tracking systems,
* High power lasers

We're open to both single and double-sided designs - happy to be convinced either way.

P.S. Another group is working on the web page, so - alas - our web site is currently of no use for images/ideas...

Target Market(s)

Engineering managers,
Scientists

Contact Information for Business Card

Dr Colin Harte
R&D Engineer

colin@wombarradevices.com.au
0427 563 710

PO Box XXX (to be confirmed)
Kelsby ACT 2917
Australia

Font styles to use
Serif
Sans Serif

Colors

Designer to choose colors to be used in the design.

Requirements
Must have
• My contact details!
• I've had many (great) "bold and plain" designs submitted already, so feel free to be artistically creative :)
• Happy to take advice re fonts/colours/printability etc.
Nice to have
• I'm not sure if "lists" are more at home on a CV than a business card, but representative services include:
• Applied electromagnetics
• RF and high speed electronics
• Signal and image processing
• Electro-optical and laser systems
• Concept-to-prototype design services
• If you're considering double sided cards, then often measuring/alignment grids/rulers feature on the back of similar cards.
• e.g. https://www.veltranoptics.example/newgrouppage9.cfm?objectgroup_id=4183
• https://www.veltranoptics.example/newgrouppage9.cfm?objectgroup_ID=4185
• ..or even a "Smith chart" (google will return lots)
• Generic images to represent a capability might work - googling images associated with keyword for each of these areas might help:
• - "passive radar", "phased array", "fdtd", "vircator"
• RF and high speed electronic design
• - "smith chart", "microstrip circuits", "dimensioned drawing", "electronic schematic"
• - "dft", "iir filter"
• - "optical cavity". "laser energy level diagram"
• Background/watermarked images outlines/wireframes/schematics would probably look OK.
Should not have
• If a list of projects/services is provided, it is important not to make the client feel that this is "all" the company can do. Engineering design is a creative discipline (like graphics :)
• Please, no stock "military" snaps like planes, missiles, etc!

```html
<!DOCTYPE html>
<html lang="en">
<head>
<meta charset="utf-8">
<title>Wombarra Devices – Business Card</title>
<link href="https://fonts.googleapis.com/css2?family=Montserrat:wght@400;500;700;800&display=swap" rel="stylesheet">
<style>
  :root {
    --backdrop: #2b2b2d;
    --navy: #1d2466;
    --navy-deep: #121848;
    --navy-mid: #1b2470;
    --blue-bright: #2f48b8;
    --paper: #f4f4f2;
    --white: #ffffff;
  }
  * { margin: 0; padding: 0; box-sizing: border-box; }
  html, body {
    width: 1200px; height: 901px; overflow: hidden;
    background: var(--backdrop);
    font-family: "Montserrat", Arial, sans-serif;
  }
  .stage { position: relative; width: 1200px; height: 901px; }
  .card {
    position: absolute; left: 290px;
    width: 620px; height: 379px;
    overflow: hidden;
  }
  .card--back { top: 56px; }
  .card--front { top: 465px; background: var(--paper); color: var(--navy); }

  .back-field {
    position: absolute; inset: 0;
    background:
      radial-gradient(ellipse 60% 70% at 85% 85%, rgba(60, 90, 210, 0.55), transparent 70%),
      radial-gradient(ellipse 50% 60% at 10% 15%, rgba(10, 14, 50, 0.6), transparent 70%),
      linear-gradient(125deg, var(--navy-deep) 0%, var(--navy-mid) 50%, var(--blue-bright) 100%);
  }
  .brand {
    position: absolute; display: flex; align-items: center; gap: 12px;
    font-weight: 700; text-transform: uppercase; line-height: 1;
  }
  .brand__dot { width: 58px; height: 58px; border-radius: 50%; flex: none; }
  .brand__name { display: flex; flex-direction: column; gap: 7px; }
  .brand__main { font-size: 27px; letter-spacing: 0.5px; }
  .brand__sub { font-size: 14px; letter-spacing: 4.5px; }

  .card--back .brand { left: 255px; top: 150px; color: var(--white); }
  .card--back .brand__dot { background: var(--white); }

  .card--front .brand { left: 318px; top: 72px; color: var(--navy); }
  .card--front .brand__dot { background: var(--navy); width: 64px; height: 64px; }

  .person { position: absolute; left: 40px; top: 168px; }
  .person__name { font-weight: 800; font-size: 22px; letter-spacing: 0.5px; text-transform: uppercase; }
  .person__role { font-weight: 500; font-size: 14px; margin-top: 2px; }

  .divider {
    position: absolute; left: 40px; right: 40px; top: 222px;
    height: 1.5px; background: var(--navy);
  }
  .contacts { position: absolute; left: 40px; top: 240px; font-size: 14px; font-weight: 500; }
  .contacts__row { display: flex; align-items: center; gap: 8px; height: 22px; }
  .contacts__row svg { width: 12px; height: 12px; fill: var(--navy); flex: none; }

  .address {
    position: absolute; left: 400px; top: 290px;
    font-size: 14px; font-weight: 500; line-height: 22px; font-style: normal;
  }
</style>
</head>
<body>
<main class="stage">
  <section class="card card--back">
    <div class="back-field" role="img" aria-label="Tone-on-tone embossed repeating pattern across a deep blue field"></div>
    <div class="brand">
      <span class="brand__dot"></span>
      <span class="brand__name">
        <span class="brand__main">Wombarra</span>
        <span class="brand__sub">Devices</span>
      </span>
    </div>
  </section>

  <section class="card card--front">
    <div class="brand">
      <span class="brand__dot"></span>
      <span class="brand__name">
        <span class="brand__main">Wombarra</span>
        <span class="brand__sub">Devices</span>
      </span>
    </div>

    <div class="person">
      <h1 class="person__name">Dr Colin Harte</h1>
      <p class="person__role">R&amp;D Engineer</p>
    </div>

    <div class="divider"></div>

    <div class="contacts">
      <p class="contacts__row">
        <svg viewBox="0 0 24 24" aria-hidden="true"><path d="M6.6 10.8c1.4 2.8 3.8 5.1 6.6 6.6l2.2-2.2c.3-.3.7-.4 1-.2 1.1.4 2.3.6 3.6.6.6 0 1 .4 1 1V20c0 .6-.4 1-1 1C10.6 21 3 13.4 3 4c0-.6.4-1 1-1h3.5c.6 0 1 .4 1 1 0 1.3.2 2.5.6 3.6.1.3 0 .7-.2 1z"/></svg>
        0427 563 710
      </p>
      <p class="contacts__row">
        <svg viewBox="0 0 24 24" aria-hidden="true"><path d="M2 5h20L12 12.5z M2 7l10 7.5L22 7v12H2z"/></svg>
        colin@wombarradevices.com.au
      </p>
    </div>

    <address class="address">
      PO Box XXX<br>
      Kelsby ACT 2917, Australia
    </address>
  </section>
</main>
</body>
</html>
```